Webdesign für Projektmanagement
Zielgruppe
Projektmanagement und Projektsteuerung von Bauvorhaben für Projektentwickler und Bauträger.
Wesentliche Bereiche sind Wirtschaftliche Steuerung, Steuerung der Baustelle und Bauabläufe sowie Steuerung der Marketing und Vertriebsaktivitäten.
Aufgabenstellung
Orientierung am Logo. Logo und Visitenkarte liegen bei. Schriftart Prelo und Prelo Slab.

```html
<!DOCTYPE html>
<html lang="de">
<head>
<meta charset="utf-8">
<title>Kernfeld Real Estate – Projekte & Referenzen</title>
<link href="https://fonts.googleapis.com/css2?family=Raleway:ital,wght@0,300;0,400;0,500;0,600;0,700;1,400&display=swap" rel="stylesheet">
<style>
:root{
  --stage:#031624;
  --navy:#0f2a44;
  --gold:#a8945a;
  --gold-bg:#b9a566;
  --gold-light:#cbbb83;
  --paper:#f6f4ef;
  --white:#ffffff;
  --line:#ecebe7;
  --text:#3a3f47;
}
*{box-sizing:border-box;margin:0;padding:0}
html,body{width:1004px;height:1200px;overflow:hidden;background:var(--stage);font-family:"Raleway",sans-serif;color:var(--text)}
.screen{position:absolute;left:53px;width:898px;height:518px;overflow:hidden;display:flex;background:var(--white)}
.screen--team{top:53px}
.screen--projects{top:608px;height:517px}
.sidebar{position:relative;width:138px;flex:none;background:var(--white)}
.brand{position:absolute;left:21px;top:58px;display:flex;align-items:center;gap:6px;font-family:"Raleway",sans-serif;font-weight:700;font-size:17px;color:var(--navy);line-height:1}
.brand__mark{width:9px;height:9px;background:var(--navy)}
.nav{position:absolute;top:127px;left:0;right:0;list-style:none;border-top:1px solid var(--line)}
.nav li{height:27.5px;border-bottom:1px solid var(--line);display:flex;align-items:center;justify-content:space-between;padding:0 15px 0 21px;font-size:8px;letter-spacing:.4px;color:var(--navy);font-weight:500}
.nav li.is-active{color:var(--gold);font-weight:600}
.nav li.search{font-style:italic;color:#8a8f96;font-weight:400;justify-content:flex-start;gap:7px;letter-spacing:0;font-size:7.6px}
.social{position:absolute;left:30px;top:491px;display:flex;gap:10px}
.social span{width:8px;height:8px;border-radius:50%;background:var(--navy)}
.main{position:relative;flex:1;background:radial-gradient(circle at 80% 60%,rgba(255,255,255,.12),transparent 30%),radial-gradient(circle at 20% 50%,rgba(255,255,255,.1),transparent 25%),linear-gradient(160deg,var(--gold-light),var(--gold-bg) 40%,#b09b5c);}
.topbar{height:26px;background:rgba(255,255,255,.14);display:flex;align-items:center;gap:16px;padding-left:47px;font-size:7.4px;color:var(--white)}
.topbar span{display:flex;align-items:center;gap:4px}
.topbar svg{width:9px;height:9px}
.eyebrow{position:absolute;left:47px;top:119px;font-size:14.5px;font-weight:600;color:var(--navy);letter-spacing:.2px}
.title{position:absolute;left:45px;top:144px;font-size:43px;font-weight:300;color:var(--white);letter-spacing:1px;white-space:nowrap}
.card{position:absolute;background:var(--paper)}
.card--intro{left:47px;top:222px;width:325px;height:320px;padding:22px 15px}
.card h2{font-size:12.6px;font-weight:500;color:var(--navy);letter-spacing:.8px;line-height:19px;margin-bottom:12px}
.card p{font-size:8.6px;line-height:12.7px;margin-bottom:8px}
.person{left:388px;width:325px;height:126px;display:flex}
.person__photo{width:139px;height:100%;background:linear-gradient(135deg,#2b2b2b,#8a8a8a 60%,#d8d8d8)}
.person__info{padding:19px 12px;font-size:8.6px;line-height:12.7px}
.person__info h3{font-size:10px;font-weight:600;color:var(--navy);letter-spacing:.8px;line-height:12px}
.person__info em{display:block;margin-bottom:10px;color:#555}
.project{left:47px;width:665px;height:190px;display:flex}
.project__body{width:341px;padding:14px 15px}
.project__body small{font-size:7.6px;font-style:italic;color:#777}
.project__body h2{font-size:12.6px;font-weight:600;letter-spacing:1px;margin:0 0 9px;line-height:15px}
.project__body p{margin-bottom:11px;max-width:250px}
.checks{list-style:none;font-size:8.6px}
.checks li{display:flex;align-items:center;gap:7px;height:20.5px}
.project__image{flex:1}
</style>
</head>
<body>

<section class="screen screen--team">
  <aside class="sidebar">
    <div class="brand"><span class="brand__mark"></span>Kernfeld</div>
    <ul class="nav">
      <li>HOME</li><li>LEISTUNGEN</li><li class="is-active">ÜBER UNS<span>›</span></li><li>PROJEKTE<span>›</span></li><li>PARTNER</li><li>KONTAKT</li>
      <li class="search"><svg width="7" height="7" viewBox="0 0 10 10"><circle cx="4" cy="4" r="3" fill="none" stroke="#a8945a" stroke-width="1.5"/><path d="M6 6l3 3" stroke="#a8945a" stroke-width="1.5"/></svg>Suchen</li>
    </ul>
    <div class="social"><span></span><span></span><span></span><span></span></div>
  </aside>
  <div class="main">
    <div class="topbar">
      <span><svg viewBox="0 0 10 10"><path d="M2 1l2 2-1 1.5c.7 1.3 1.3 2 2.5 2.5L7 6l2 2-1.5 1.5C4.5 9 1 5.5.5 2.5z" fill="#0f2a44"/></svg>+49 (0)211 - 555 010 20</span>
      <span><svg viewBox="0 0 10 10"><circle cx="5" cy="5" r="4" fill="none" stroke="#0f2a44"/><path d="M5 2.5V5h2" fill="none" stroke="#0f2a44"/></svg>Mo - Fr 9:00 - 18:00</span>
      <span><svg viewBox="0 0 10 10"><rect x="1" y="2.5" width="8" height="5" fill="none" stroke="#0f2a44"/><path d="M1 2.5l4 3 4-3" fill="none" stroke="#0f2a44"/></svg>info@kernfeld-re.de</span>
      <span><svg viewBox="0 0 10 10"><path d="M5 9.5S2 6 2 4a3 3 0 016 0c0 2-3 5.5-3 5.5z" fill="#0f2a44"/><circle cx="5" cy="4" r="1" fill="#cbbb83"/></svg>Lindenallee 12, 40210 Düsseldorf</span>
    </div>
    <h2 class="eyebrow">KERNFELD REAL ESTATE</h2>
    <h1 class="title">PROJEKTE &amp; REFERENZEN</h1>
    <article class="card card--intro">
      <h2>PROJEKTMANAGEMENT UND PROJEKTSTEUERUNG VON BAUVORHABEN</h2>
      <p>Die zunehmende Urbanisierung hat den Immobilienmarkt in den letzten Jahren nachhaltig verändert. Als Teil des größten Ballungszentrums Europas, hat dies starke Auswirkungen auf die Metropolregion Köln, Düsseldorf und Bonn. Begleitet wird diese Entwicklung durch vielschichtige städtebauliche Maßnahmen in der Region.</p>
      <p>Die Konsequenz aus dieser Entwicklung ist ein hoher Investitions-, Umnutzungs- und Projektentwicklungsbedarf bei Immobilien. Daraus entstanden ist ein für Investoren strukturell attraktiver Markt.</p>
      <p>In diesem Umfeld bietet die Kernfeld Real Estate GmbH ihren Kunden maßgeschneiderte Dienstleistungen für Immobilienportfolios an.</p>
      <p>Lorem ipsum dolor sit amet, consetetur sadipscing elitr, sed diam nonumy eirmod tempor invidunt ut labore et dolore magna aliquyam erat, sed diam voluptua. At vero eos et accusam et justo duo dolores et ea rebum. Stet clita kasd gubergren, no sea takimata sanctus est Lorem ipsum dolor sit amet. Lorem ipsum dolor sit amet, consetetur sadipscing elitr, sed diam nonumy eirmod tempor invidunt ut labore et dolore magna aliquyam erat,</p>
    </article>
    <article class="card person" style="top:222px">
      <div class="person__photo" role="img" aria-label="Schwarzweiß-Porträt des Geschäftsführers Malte Riedbusch"></div>
      <div class="person__info"><h3>MALTE RIEDBUSCH</h3><em>Geschäftsführer</em>E-Mail: malte.riedbusch@kernfeld-re.de<br>Mobil: +49 170 55 01 234</div>
    </article>
    <article class="card person" style="top:360px">
      <div class="person__photo" role="img" aria-label="Schwarzweiß-Porträt des Geschäftsführers Jonas Albrecht vor einer Treppe"></div>
      <div class="person__info"><h3>JONAS ALBRECHT</h3><em>Geschäftsführer</em>E-Mail: jonas.albrecht@kernfeld-re.de<br>Mobil: +49 160 55 02 345</div>
    </article>
  </div>
</section>

<section class="screen screen--projects">
  <aside class="sidebar">
    <div class="brand"><span class="brand__mark"></span>Kernfeld</div>
    <ul class="nav">
      <li>HOME</li><li>LEISTUNGEN</li><li class="is-active">ÜBER UNS<span>›</span></li><li>PROJEKTE<span>›</span></li><li>PARTNER</li><li>KONTAKT</li>
      <li class="search"><svg width="7" height="7" viewBox="0 0 10 10"><circle cx="4" cy="4" r="3" fill="none" stroke="#a8945a" stroke-width="1.5"/><path d="M6 6l3 3" stroke="#a8945a" stroke-width="1.5"/></svg>Suchen</li>
    </ul>
    <div class="social"><span></span><span></span><span></span><span></span></div>
  </aside>
  <div class="main">
    <div class="topbar">
      <span><svg viewBox="0 0 10 10"><path d="M2 1l2 2-1 1.5c.7 1.3 1.3 2 2.5 2.5L7 6l2 2-1.5 1.5C4.5 9 1 5.5.5 2.5z" fill="#0f2a44"/></svg>+49 (0)211 - 555 010 20</span>
      <span><svg viewBox="0 0 10 10"><circle cx="5" cy="5" r="4" fill="none" stroke="#0f2a44"/><path d="M5 2.5V5h2" fill="none" stroke="#0f2a44"/></svg>Mo - Fr 9:00 - 18:00</span>
      <span><svg viewBox="0 0 10 10"><rect x="1" y="2.5" width="8" height="5" fill="none" stroke="#0f2a44"/><path d="M1 2.5l4 3 4-3" fill="none" stroke="#0f2a44"/></svg>info@kernfeld-re.de</span>
      <span><svg viewBox="0 0 10 10"><path d="M5 9.5S2 6 2 4a3 3 0 016 0c0 2-3 5.5-3 5.5z" fill="#0f2a44"/><circle cx="5" cy="4" r="1" fill="#cbbb83"/></svg>Lindenallee 12, 40210 Düsseldorf</span>
    </div>
    <h2 class="eyebrow">KERNFELD REAL ESTATE</h2>
    <h1 class="title">PROJEKTE &amp; REFERENZEN</h1>
    <article class="card project" style="top:222px">
      <div class="project__body">
        <small>Immobilienmanagement</small>
        <h2>PROJEKTNAME</h2>
        <p>Begleitung einer Portfolioliquidierung eines luxemburgischen institutionellen Investors</p>
        <ul class="checks">
          <li><svg width="9" height="9" viewBox="0 0 10 10"><path d="M1 5.5l2.5 2.5L9 1.5" fill="none" stroke="#0f2a44" stroke-width="2"/></svg>Portfolio-Analyse</li>
          <li><svg width="9" height="9" viewBox="0 0 10 10"><path d="M1 5.5l2.5 2.5L9 1.5" fill="none" stroke="#0f2a44" stroke-width="2"/></svg>Begleitung der Immobilientransaktionen</li>
          <li><svg width="9" height="9" viewBox="0 0 10 10"><path d="M1 5.5l2.5 2.5L9 1.5" fill="none" stroke="#0f2a44" stroke-width="2"/></svg>Reporting</li>
        </ul>
      </div>
      <div class="project__image" role="img" aria-label="Foto eines modernen Wohnhauses mit Balkonen unter blauem Himmel" style="background:linear-gradient(180deg,#9fb6cc,#b9b4aa 45%,#8c8880 80%,#9aa466)"></div>
    </article>
    <article class="card project" style="top:428px">
      <div class="project__body">
        <small>Immobiliensanierung</small>
        <h2>PROJEKTNAME</h2>
        <p>Begleitung einer Portfolioliquidierung eines luxemburgischen institutionellen Investors</p>
        <ul class="checks">
          <li><svg width="9" height="9" viewBox="0 0 10 10"><path d="M1 5.5l2.5 2.5L9 1.5" fill="none" stroke="#0f2a44" stroke-width="2"/></svg>Portfolio-Analyse</li>
        </ul>
      </div>
      <div class="project__image" role="img" aria-label="Foto eines sanierten Altbaus mit Bäumen unter bewölktem Himmel" style="background:linear-gradient(180deg,#b9cde0,#dfe6ea 40%,#5f7f45 75%,#3f5e2e)"></div>
    </article>
  </div>
</section>

</body>
</html>
```